Corporate-Design für Steuerberatungsgesellschaft
Zielgruppe
Wir sind eine Steuerberatungsgesellschaft mit 10 Mitarbeitern im Norden von Deutschland, kurz vor der Ostseeküste. Unser Unternehmen besteht seit 30 Jahren. Wir betreuen vor allem Mandanten in kleinen und mittleren Unternehmen: von der Arztpraxis bis zum Bauunternehmen. Demnächst werden wir neue Räume beziehen. Diese sollen großzügiger und moderner werden, teilweise mit Glaswänden.
Aufgabenstellung
Unser bisheriges Farbkonzept war von bordeaux und creme geprägt (www.kanzlei-mervato.de). Das muss aber nicht weiter bestehen. Das bisherige Logo finden wir inhaltlich recht treffend, aber es sollte moderner gestaltet werden. Der Schriftzug des Kanzleinamens soll an der Fassade in silbernen Buchstaben angebracht werden.

```html
<!DOCTYPE html>
<html lang="de">
<head>
<meta charset="utf-8">
<title>KSB Wendorf – Geschäftsausstattung</title>
<link href="https://fonts.googleapis.com/css2?family=Noto+Serif:wght@400;700&display=swap" rel="stylesheet">
<style>
  :root{
    --ink:#363b39;
    --blue:#1386b5;
    --paper:#ffffff;
    --bg:#f8f6f6;
    --muted:#4a4f4d;
  }
  *{margin:0;padding:0;box-sizing:border-box}
  html,body{width:1200px;height:720px;overflow:hidden;background:var(--bg);font-family:"Noto Serif",serif;color:var(--ink)}
  .canvas{position:relative;width:1200px;height:720px}
  .mark-square{display:inline-block;background:var(--blue)}

  /* Primary wordmark */
  .brand{position:absolute;left:80px;top:150px;display:flex;align-items:center;gap:22px}
  .brand .mark-square{width:70px;height:70px}
  .brand-name{font-size:64px;font-weight:400;letter-spacing:2px;color:var(--ink);line-height:1}

  /* Business card front */
  .card{position:absolute;width:206px;height:130px;overflow:hidden}
  .card-front{left:508px;top:356px;background:var(--paper)}
  .card-front .title{position:absolute;left:16px;top:9px;font-size:5.5px;color:var(--muted)}
  .card-front .person{position:absolute;left:15px;top:15px;font-size:9px;font-weight:700;color:var(--blue)}
  .card-front .role{position:absolute;left:16px;top:26px;font-size:5.5px;color:var(--muted)}
  .card-front .address{position:absolute;left:101px;top:55px;font-size:5px;line-height:7.8px;color:var(--muted)}
  .card-front .contacts{position:absolute;left:101px;top:95px}
  .card-front .accent{position:absolute;left:78px;bottom:0;width:128px;height:3px;background:var(--blue)}
  .card-front .mark-square{position:absolute;left:16px;top:62px;width:40px;height:40px}

  .contact-list{list-style:none;font-size:5px;color:var(--muted)}
  .contact-list li{display:flex;align-items:center;gap:5px;height:7.4px}
  .contact-list svg{width:5px;height:5px;flex:none}

  /* Business card back */
  .card-back{left:508px;top:548px;height:131px;background:var(--ink)}
  .card-back .brand-small{position:absolute;left:28px;top:52px;display:flex;align-items:center;gap:8px}
  .card-back .mark-square{width:20px;height:20px}
  .card-back .brand-small span{font-size:17px;color:#fff;letter-spacing:.5px}
  .card-back .services{position:absolute;left:13px;top:110px;font-size:4.6px;line-height:7.2px;color:#e4e6e5}
  .card-back .accent{position:absolute;left:0;bottom:0;width:110px;height:3px;background:var(--blue)}

  /* Letterhead */
  .letter{position:absolute;left:752px;top:141px;width:385px;height:540px;background:var(--paper)}
  .letter .brand-head{position:absolute;right:20px;top:13px;display:flex;align-items:center;gap:7px}
  .letter .brand-head .mark-square{width:24px;height:24px}
  .letter .brand-head span{font-size:19px;letter-spacing:.5px}
  .letter .sender{position:absolute;left:39px;top:80px;font-size:4.8px;line-height:7.2px;color:var(--muted)}
  .letter .sender b{color:var(--ink)}
  .letter .contacts{position:absolute;left:258px;top:74px}
  .letter .contact-list{font-size:5.8px}
  .letter .contact-list li{height:8.6px}
  .letter .rule{position:absolute;left:30px;top:484px;width:311px;height:1.5px;background:var(--blue)}
  .letter .footer{position:absolute;left:31px;top:489px;display:flex;gap:0;font-size:4.6px;line-height:7.2px;color:var(--muted)}
  .letter .footer div{width:118px}
  .letter .footer div:nth-child(2){width:110px}
  .letter .footer b{color:var(--ink)}
</style>
</head>
<body>
<main class="canvas">

  <header class="brand">
    <span class="mark-square"></span>
    <span class="brand-name">KSB WENDORF</span>
  </header>

  <section class="card card-front">
    <p class="title">Diplom-Kaufmann</p>
    <p class="person">Jonas Berthold - Ahlert</p>
    <p class="role">Geschäftsführer / Steuerberater</p>
    <span class="mark-square"></span>
    <p class="address">KSB Wendorf<br>Steuerberatungsgesellschaft mbH<br>Lindenweg 12<br>17000 Musterstadt</p>
    <ul class="contact-list contacts">
      <li><svg viewBox="0 0 10 10"><circle cx="5" cy="5" r="5" fill="#1386b5"/><path d="M3 2.5l1 1-.6.8c.4.9 1 1.5 1.9 1.9l.8-.6 1 1-.6 1C4.8 7.5 2.5 5.2 2.4 3.1z" fill="#fff"/></svg>+49 (0) 3900 / 55 10 - 0</li>
      <li><svg viewBox="0 0 10 10"><circle cx="5" cy="5" r="5" fill="#1386b5"/><rect x="3" y="4" width="4" height="3" fill="#fff"/></svg>+49 (0) 3900 / 55 10 - 14</li>
      <li><svg viewBox="0 0 10 10"><circle cx="5" cy="5" r="5" fill="#1386b5"/><rect x="2.8" y="3.4" width="4.4" height="3.2" fill="#fff"/></svg>kontakt@kanzlei-mervato.de</li>
      <li><svg viewBox="0 0 10 10"><circle cx="5" cy="5" r="5" fill="#1386b5"/><circle cx="5" cy="5" r="2.3" fill="none" stroke="#fff" stroke-width=".8"/></svg>www.kanzlei-mervato.de</li>
    </ul>
    <span class="accent"></span>
  </section>

  <section class="card card-back">
    <div class="brand-small"><span class="mark-square"></span><span>KSB WENDORF</span></div>
    <p class="services">Steuerberatung / Finanz- und Lohnbuchhaltung<br>Betriebswirtschaftliche Beratung</p>
    <span class="accent"></span>
  </section>

  <section class="letter">
    <div class="brand-head"><span class="mark-square"></span><span>KSB WENDORF</span></div>
    <p class="sender"><b>KSB Wendorf Steuerberatungsgesellschaft mbH</b><br>Lindenweg 12 / 17000 Musterstadt</p>
    <ul class="contact-list contacts">
      <li><svg viewBox="0 0 10 10"><circle cx="5" cy="5" r="5" fill="#1386b5"/><path d="M3 2.5l1 1-.6.8c.4.9 1 1.5 1.9 1.9l.8-.6 1 1-.6 1C4.8 7.5 2.5 5.2 2.4 3.1z" fill="#fff"/></svg>+49 (0) 3900 / 55 10 - 0</li>
      <li><svg viewBox="0 0 10 10"><circle cx="5" cy="5" r="5" fill="#1386b5"/><rect x="3" y="4" width="4" height="3" fill="#fff"/></svg>+49 (0) 3900 / 55 10 - 14</li>
      <li><svg viewBox="0 0 10 10"><circle cx="5" cy="5" r="5" fill="#1386b5"/><rect x="2.8" y="3.4" width="4.4" height="3.2" fill="#fff"/></svg>kontakt@kanzlei-mervato.de</li>
      <li><svg viewBox="0 0 10 10"><circle cx="5" cy="5" r="5" fill="#1386b5"/><circle cx="5" cy="5" r="2.3" fill="none" stroke="#fff" stroke-width=".8"/></svg>www.kanzlei-mervato.de</li>
    </ul>
    <span class="rule"></span>
    <footer class="footer">
      <div><b>KSB Wendorf<br>Steuerberatungsgesellschaft mbH</b><br>Lindenweg 12<br>17000 Musterstadt<br><b>USt-IdNr.</b> DE000000000<br>AG Musterstadt / HRB 1234</div>
      <div><b>Geschäftsführer:</b><br>Jonas Berthold - Ahlert<br>Steuerberater / Dipl. Kaufmann<br><br>Lukas Tamm<br>Steuerberater</div>
      <div><b>Bankverbindung:</b><br>Bank Lindmar Musterstadt<br><b>IBAN</b> DE00 0000 0000 0000 0000 00<br><b>BIC</b>&nbsp; MUSTDEXXXX</div>
    </footer>
  </section>

</main>
</body>
</html>
```